Brivora Distance Learning Website

Brivora provide e-learning and mixed learning solutions for individuals, colleges, organisations and B2B.
We need a modern, light and flat website design for Brivora. We want to to see the designer incorporate user experience(UX) design elements into the AI or PSD mockups. We would like to see designs that use pastel colors that compliment yellow and black of our logo.
We want our E-learning experience to accelerate learning and for the interface to be user friendly and intuitive. We want the designs to focus on quick access to course information, course reviews, learning progress and study advice. Quick and intuitive access to all content for our clients is one of our top priorities.
We would like designs for the following project 3 pages:
1. Learner homepage dashboard (see attached screenshot).
On this page the Learners need to:
- Login
- Have quick access to Packages and Courses.
- See other recommended courses (Below Packages and Courses)
- Possibly a left hand side column/menu with thumbnail icons (See lumeqa learner dashboard screenshot)
2. Homepage
See current sample
http://www.brivora-learn.example
We would like the designer to focus on creating a customized banner to enhance the home page.
3. Primary Landing/Marketing page
This page is geared towards customer acquisition with the focal point being the top banner (video or HD image).
And Course Preview content below.
See reference
http://brivora-learn.example/subscriptionPlans/marketing/MTc%3D/Mjc4Nw%3D%3D/Speaking%20Nepali%20%2B%20Nepali%20Snacks%20Bundle%20by%20Lorne%20Pike%20Vell
Other site we like:
- https://www.skillorva.example (We like the home page and top bar on courses page)
- http://www.tutorcrest.example
- http://pixelgrovelab.example (think this site looks great, love the lower graphics on the homepage)
Updates
Hello,
Thank you for taking the time to contribute to this web design competition. We would just like to point out a few things:
1. Please try to make the color palette similar to the colors used in the screenshot that we just uploaded ('possible color palette).
2. Please make the designs specific to each page: THE LEARNER HOMEPAGE, HOME PAGE, and the MARKETING LANDING PAGE.
We are very happy with the high quality of designs so far,
Cheers,
Ned Ru
VK-Studio
Also,
Please avoid using dark/bold elements in the designs. The ONLY elements that we want to be dark are the logo and the footer.
Any questions please ask,
Cheers,
Ned Ru
Vk-Studio
Hello,
Based on the round of feedback we just gave it would be great if you could complete further design changes by tomorrow, as we are pushed for time.
Thank you,
Ned Ru
VK-Studio

```html
<!DOCTYPE html>
<html lang="en">
<head>
<meta charset="utf-8">
<title>Brivora for Organisations and Academic Institutes</title>
<link rel="stylesheet" href="https://fonts.googleapis.com/css2?family=Arimo:wght@400;700&family=Raleway:wght@400;500&family=Baloo+2:wght@700&display=swap">
<style>
:root{
  --yellow:#f6bb22;
  --yellow-dark:#e0a60f;
  --ink:#222;
  --text:#333;
  --muted:#666;
  --line:#d6d6d6;
  --page:#ececec;
  --card:#f5f5f5;
  --white:#fff;
  --footer:#333;
  --btn-top:#8a8a8a;
  --btn-bot:#5c5c5c;
  --orange:#f0a81a;
}
*{box-sizing:border-box;margin:0;padding:0}
html,body{width:1000px;height:1200px;overflow:hidden}
body{font-family:"Arimo",Arial,sans-serif;color:var(--text);background:var(--page);position:relative}
.site-header{position:absolute;left:0;top:0;width:1000px;height:77px;background:var(--white);box-shadow:0 1px 3px rgba(0,0,0,.15);z-index:2}
.brand{position:absolute;left:88px;top:20px;display:flex;align-items:center;gap:8px;font-family:"Raleway",sans-serif;font-weight:500;font-size:30px;color:var(--ink)}
.brand-dot{width:22px;height:22px;border-radius:50%;background:var(--yellow)}
.btn-lang{position:absolute;left:718px;top:24px;width:88px;height:27px;background:var(--yellow);border-radius:2px;font-size:13px;color:var(--ink);display:flex;align-items:center;justify-content:center}
.btn-signin{position:absolute;left:831px;top:25px;width:73px;height:26px;border-radius:2px;background:linear-gradient(var(--btn-top),var(--btn-bot));color:var(--white);font-size:13px;display:flex;align-items:center;justify-content:center}
.hero{position:absolute;left:0;top:77px;width:1000px;height:478px;background:linear-gradient(100deg,#8f8880 0%,#c9c0b6 35%,#d8cfc4 60%,#b9aea2 100%)}
.hero-title{position:absolute;left:0;top:113px;width:1000px;text-align:center;font-family:"Baloo 2",sans-serif;font-weight:700;font-size:42px;line-height:54px;color:var(--yellow);text-shadow:1px 2px 3px rgba(0,0,0,.35)}
.search-panel{position:absolute;left:178px;top:249px;width:628px;height:124px;background:rgba(60,58,56,.85);border-radius:3px}
.search-panel h2{position:absolute;left:20px;top:20px;font-weight:400;font-size:22px;color:var(--white);font-family:"Arimo",sans-serif}
.search-field{position:absolute;left:20px;top:61px;width:526px;height:38px;background:var(--white);border-radius:2px 0 0 2px}
.search-btn{position:absolute;left:546px;top:61px;width:50px;height:38px;background:var(--yellow);border-radius:0 2px 2px 0;display:flex;align-items:center;justify-content:center}
.beta-tab{position:absolute;left:960px;top:280px;width:40px;height:135px;background:var(--yellow);border-radius:4px 0 0 4px;display:flex;align-items:center;justify-content:center}
.beta-tab span{transform:rotate(-90deg);white-space:nowrap;font-size:19px;color:var(--ink)}
.section-title{position:absolute;left:83px;top:585px;width:834px;display:flex;align-items:center;gap:6px}
.section-title::before,.section-title::after{content:"";flex:1;height:1px;background:#aaa}
.section-title h2{font-family:"Raleway",sans-serif;font-weight:400;font-size:33px;color:#3a3a3a}
.categories{position:absolute;left:83px;top:667px;width:197px;height:408px;background:var(--white);box-shadow:0 1px 2px rgba(0,0,0,.12)}
.categories h3{height:42px;background:var(--yellow);border-radius:3px 3px 0 0;font-family:"Raleway",sans-serif;font-weight:500;font-size:20px;color:var(--ink);padding:9px 12px}
.categories ul{list-style:none}
.categories li{height:35.3px;border-bottom:1px solid #e4e4e4;font-size:12px;color:var(--ink);padding:13px 0 0 22px;position:relative}
.categories li::before{content:"";position:absolute;left:12px;top:19px;border-left:3px solid #555;border-top:2px solid transparent;border-bottom:2px solid transparent}
.categories li:last-child{border-bottom:none}
.package{position:absolute;top:667px;width:185px;height:335px;background:var(--card);border:1px solid #d0d0d0;border-radius:3px;box-shadow:0 1px 2px rgba(0,0,0,.1)}
.package-cover{position:absolute;left:8px;top:8px;width:165px;height:142px;background:linear-gradient(#f7c02b,#f4b41c)}
.package-cover .cover-title{position:absolute;left:0;top:70px;width:100%;text-align:center;color:var(--white);font-family:"Raleway",sans-serif;font-weight:500;font-size:17px;letter-spacing:1px}
.package-stats{position:absolute;left:0;top:158px;width:183px;height:37px;border-top:1px solid #ccc;border-bottom:1px solid #ccc;background:#ececec;display:flex}
.stat-cat{width:89px;border-right:1px solid #ccc;font-size:11px;padding:7px 0 0 17px;line-height:13px;color:var(--ink)}
.stat-views{flex:1;text-align:center;font-size:11.5px;font-weight:700;color:var(--ink);padding-top:3px}
.package-reviews{position:absolute;top:207px;left:0;width:100%;text-align:center;font-size:11px;color:var(--ink)}
.stars{display:flex;justify-content:center;gap:1px;margin-top:3px}
.package-name{position:absolute;left:14px;top:246px;width:160px;font-size:11px;line-height:14px;color:var(--ink)}
.package-name small{font-size:9px;color:var(--muted)}
.btn-details{position:absolute;left:12px;top:299px;width:157px;height:28px;border-radius:3px;background:linear-gradient(var(--btn-top),var(--btn-bot));color:var(--white);font-size:10.5px;font-weight:700;display:flex;align-items:center;justify-content:center;gap:6px}
.org-note{position:absolute;left:308px;top:1024px;width:600px}
.org-note h3{font-family:"Raleway",sans-serif;font-weight:500;font-size:16px;color:var(--orange)}
.org-note p{margin-top:5px;font-size:11.5px;line-height:17px;color:var(--ink)}
.site-footer{position:absolute;left:0;top:1117px;width:1000px;height:83px;background:var(--footer)}
.footer-links{position:absolute;left:91px;top:15px;list-style:none;font-size:11.5px;line-height:18px;color:#ddd}
.footer-brand{position:absolute;left:748px;top:24px;display:flex;align-items:center;gap:8px;font-family:"Raleway",sans-serif;font-weight:500;font-size:30px;color:var(--white)}
</style>
</head>
<body>
<header class="site-header">
  <div class="brand"><span class="brand-dot"></span>Brivora</div>
  <div class="btn-lang">English(US)</div>
  <div class="btn-signin">Sign In</div>
</header>

<section class="hero" role="img" aria-label="Blurred photo of a man working at a laptop">
</section>
<h1 class="hero-title">Brivora for Organisations and<br>Academic Institutes</h1>
<div class="search-panel">
  <h2>What Can We Help You Learn Today?</h2>
  <div class="search-field"></div>
  <div class="search-btn">
    <svg width="24" height="24" viewBox="0 0 24 24"><circle cx="10" cy="10" r="7.5" fill="none" stroke="#111" stroke-width="2.6"/><line x1="15.5" y1="15.5" x2="21.5" y2="21.5" stroke="#111" stroke-width="3" stroke-linecap="round"/></svg>
  </div>
</div>
<div class="beta-tab"><span>Join Beta</span></div>

<div class="section-title"><h2>Learning Packages</h2></div>

<aside class="categories">
  <h3>Categories</h3>
  <ul>
    <li>Business and Finance</li>
    <li>Marketing</li>
    <li>IT &amp; Software</li>
    <li>Lifestyle</li>
    <li>Personal Development</li>
    <li>Photography</li>
    <li>Health and Fitness</li>
    <li>Education and Teaching</li>
    <li>Music</li>
    <li>Hotels and Hospitality</li>
  </ul>
</aside>

<article class="package" style="left:308px">
  <div class="package-cover" role="img" aria-label="Course cover artwork for Nepali Snacks"><div class="cover-title">Nepali Snacks</div></div>
  <div class="package-stats"><div class="stat-cat">Language and...</div><div class="stat-views"><svg width="14" height="9" viewBox="0 0 14 9"><ellipse cx="7" cy="4.5" rx="6" ry="3.8" fill="none" stroke="#555" stroke-width="1.4"/><circle cx="7" cy="4.5" r="1.7" fill="#555"/></svg><br>Views 1417</div></div>
  <div class="package-reviews">Reviews
    <div class="stars"><svg width="68" height="12" viewBox="0 0 68 12"><g fill="#f4b41c" stroke="#b9860c" stroke-width=".6"><polygon id="s" points="6,0.5 7.6,4.2 11.5,4.4 8.5,6.9 9.5,11 6,8.7 2.5,11 3.5,6.9 0.5,4.4 4.4,4.2"/><use href="#s" x="14"/><use href="#s" x="28"/><use href="#s" x="42"/></g><use href="#s" x="56" fill="#999" stroke="none"/></svg></div>
  </div>
  <div class="package-name">Speaking Nepali Fundamentals Suite by Lorne Pike Vell<br>by <small>Lorne Vell</small></div>
  <div class="btn-details"><svg width="18" height="8" viewBox="0 0 18 8"><rect width="7" height="8" fill="#fff"/><rect x="9" y="1" width="9" height="1.4" fill="#fff"/><rect x="9" y="3.3" width="9" height="1.4" fill="#fff"/><rect x="9" y="5.6" width="9" height="1.4" fill="#fff"/></svg>DETAILS</div>
</article>

<article class="package" style="left:520px">
  <div class="package-cover" role="img" aria-label="Course cover artwork for Nepali Snacks"><div class="cover-title">Nepali Snacks</div></div>
  <div class="package-stats"><div class="stat-cat">Language and...</div><div class="stat-views"><svg width="14" height="9" viewBox="0 0 14 9"><ellipse cx="7" cy="4.5" rx="6" ry="3.8" fill="none" stroke="#555" stroke-width="1.4"/><circle cx="7" cy="4.5" r="1.7" fill="#555"/></svg><br>Views 1417</div></div>
  <div class="package-reviews">Reviews
    <div class="stars"><svg width="68" height="12" viewBox="0 0 68 12"><g fill="#f4b41c" stroke="#b9860c" stroke-width=".6"><use href="#s"/><use href="#s" x="14"/><use href="#s" x="28"/><use href="#s" x="42"/></g><use href="#s" x="56" fill="#999" stroke="none"/></svg></div>
  </div>
  <div class="package-name">Speaking Nepali Fundamentals Suite by Lorne Pike Vell<br>by <small>Lorne Vell</small></div>
  <div class="btn-details"><svg width="18" height="8" viewBox="0 0 18 8"><rect width="7" height="8" fill="#fff"/><rect x="9" y="1" width="9" height="1.4" fill="#fff"/><rect x="9" y="3.3" width="9" height="1.4" fill="#fff"/><rect x="9" y="5.6" width="9" height="1.4" fill="#fff"/></svg>DETAILS</div>
</article>

<article class="package" style="left:732px">
  <div class="package-cover" role="img" aria-label="Course cover artwork for Nepali Snacks"><div class="cover-title">Nepali Snacks</div></div>
  <div class="package-stats"><div class="stat-cat">Language and...</div><div class="stat-views"><svg width="14" height="9" viewBox="0 0 14 9"><ellipse cx="7" cy="4.5" rx="6" ry="3.8" fill="none" stroke="#555" stroke-width="1.4"/><circle cx="7" cy="4.5" r="1.7" fill="#555"/></svg><br>Views 1417</div></div>
  <div class="package-reviews">Reviews
    <div class="stars"><svg width="68" height="12" viewBox="0 0 68 12"><g fill="#f4b41c" stroke="#b9860c" stroke-width=".6"><use href="#s"/><use href="#s" x="14"/><use href="#s" x="28"/><use href="#s" x="42"/></g><use href="#s" x="56" fill="#999" stroke="none"/></svg></div>
  </div>
  <div class="package-name">Speaking Nepali Fundamentals Suite by Lorne Pike Vell<br>by <small>Lorne Vell</small></div>
  <div class="btn-details"><svg width="18" height="8" viewBox="0 0 18 8"><rect width="7" height="8" fill="#fff"/><rect x="9" y="1" width="9" height="1.4" fill="#fff"/><rect x="9" y="3.3" width="9" height="1.4" fill="#fff"/><rect x="9" y="5.6" width="9" height="1.4" fill="#fff"/></svg>DETAILS</div>
</article>

<section class="org-note">
  <h3>Learning for Organisations and Educational Institutions.</h3>
  <p>Launching Soon! - Brivora will be launching services to integrate Brivora's learning platform into Organisations and Learning Institutes to support Online, Interactive and Blended Learning.</p>
</section>

<footer class="site-footer">
  <ul class="footer-links">
    <li>Copyright © 2015 Brivora.example</li>
    <li>Terms of Use</li>
    <li>Privacy Policy</li>
  </ul>
  <div class="footer-brand"><span class="brand-dot"></span>Brivora</div>
</footer>
</body>
</html>
```